BrindleStaffing Business Card Design

We are a staffing company finding positions for dedicated nurses and physicians.

Target Market(s)

Business Professionals

Industry/Entity Type

Staffing

Contact Information for Business Card

Gordon Pratley
Chairman
417 39th Avenue South
SAINT PETERSBURG FL 33712
813-555-4172 Mobile
813-555-8036 Fax
gpratley@brindlestaffing.com
www.brindlestaffing.com

Font styles to use
Sans Serif

Colors
fbee3e
f04a50
f37122

Requirements
Must have
• Logo Attached, see colors below. We'd like to see Yellow, Orange and Red.

```html
<!DOCTYPE html>
<html lang="en">
<head>
<meta charset="utf-8">
<title>BrindleStaffing Business Card</title>
<link href="https://fonts.googleapis.com/css2?family=Open+Sans:wght@400;600;700&display=swap" rel="stylesheet">
<style>
  :root {
    --page-bg: #e9e6e1;
    --card-white: #ffffff;
    --brand-yellow: #fbee3e;
    --brand-orange: #f37122;
    --brand-red: #f04a50;
    --text-white: #ffffff;
  }
  * { box-sizing: border-box; margin: 0; padding: 0; }
  html, body {
    width: 1200px; height: 768px; overflow: hidden;
    background: var(--page-bg);
    font-family: "Open Sans", Arial, sans-serif;
  }
  .stage { position: relative; width: 1200px; height: 768px; }
  .card {
    position: absolute; top: 236px;
    width: 520px; height: 297px;
    border-radius: 18px; overflow: hidden;
    box-shadow: 0 6px 18px rgba(0,0,0,0.18);
  }
  .card--front { left: 50px; background: var(--card-white); }
  .card--back {
    left: 630px;
    background: linear-gradient(135deg, var(--brand-orange) 0%, var(--brand-red) 100%);
    display: flex; align-items: center; justify-content: center;
  }
  .brand {
    display: flex; align-items: center; justify-content: center; gap: 10px;
  }
  .card--front .brand { position: absolute; left: 0; right: 0; top: 62px; }
  .brand__dot {
    width: 16px; height: 16px; border-radius: 50%;
    background: var(--brand-yellow); flex: none;
  }
  .wordmark { font-weight: 700; letter-spacing: -1px; line-height: 1; }
  .card--front .wordmark { font-size: 48px; color: var(--brand-orange); }
  .card--back .wordmark { font-size: 52px; color: var(--text-white); }

  .info-band {
    position: absolute; left: 0; right: 0; top: 158px; height: 100px;
    display: flex;
  }
  .identity {
    width: 228px; background: var(--brand-red); color: var(--text-white);
    padding: 12px 14px 0 10px; text-align: right;
  }
  .identity__name { font-size: 19px; font-weight: 700; line-height: 1.1; }
  .identity__title { font-size: 13px; font-weight: 600; margin-bottom: 6px; }
  .identity__address { font-size: 11px; line-height: 1.35; }
  .contacts {
    flex: 1; background: var(--brand-orange); color: var(--text-white);
    list-style: none; padding: 12px 16px; font-size: 11.5px;
  }
  .contacts li { display: flex; align-items: center; gap: 7px; line-height: 1.6; }
  .contacts svg { width: 11px; height: 11px; flex: none; }
</style>
</head>
<body>
<main class="stage">
  <section class="card card--front">
    <div class="brand">
      <div class="wordmark">BrindleStaffing</div>
      <span class="brand__dot"></span>
    </div>
    <div class="info-band">
      <div class="identity">
        <p class="identity__name">Gordon Pratley</p>
        <p class="identity__title">Chairman</p>
        <p class="identity__address">417 39th Avenue South<br>SAINT PETERSBURG FL 33712</p>
      </div>
      <ul class="contacts">
        <li>
          <svg viewBox="0 0 12 12"><rect x="3" y="0.5" width="6" height="11" rx="1" fill="none" stroke="#fff" stroke-width="1.2"/><circle cx="6" cy="9.6" r="0.7" fill="#fff"/></svg>
          813-555-4172
        </li>
        <li>
          <svg viewBox="0 0 12 12"><rect x="1" y="4" width="10" height="7" rx="1" fill="#fff"/><rect x="3" y="1" width="6" height="3" fill="none" stroke="#fff" stroke-width="1"/></svg>
          813-555-8036
        </li>
        <li>
          <svg viewBox="0 0 12 12"><rect x="0.6" y="2" width="10.8" height="8" fill="none" stroke="#fff" stroke-width="1.1"/><path d="M0.8 2.4 L6 6.6 L11.2 2.4" fill="none" stroke="#fff" stroke-width="1.1"/></svg>
          gpratley@brindlestaffing.com
        </li>
        <li>
          <svg viewBox="0 0 12 12"><circle cx="6" cy="6" r="5.2" fill="none" stroke="#fff" stroke-width="1.1"/><path d="M0.8 6 H11.2 M6 0.8 C3 3.5 3 8.5 6 11.2 M6 0.8 C9 3.5 9 8.5 6 11.2" fill="none" stroke="#fff" stroke-width="0.9"/></svg>
          www.brindlestaffing.com
        </li>
      </ul>
    </div>
  </section>

  <section class="card card--back">
    <div class="brand">
      <div class="wordmark">BrindleStaffing</div>
      <span class="brand__dot"></span>
    </div>
  </section>
</main>
</body>
</html>
```